TLV Accounting Firm Needs Graphic Art for Our Proven Processes and For Our Core Values

**Looking for redesign of attached Powerpoint content (see below)
***Final graphic should be good for web use

Date: March 10, 2017

From: Colin Ashdown, CPA
Ashdown, Pettifer & Associates, P.C. (TLV)

Background:

TLV is a 20 person Houston based CPA firm, providing tax, accounting, financial and consulting services, to individuals and to entrepreneurs and their businesses. TLV is engaged in a process called KLU (See the book Headway, by Lars Obermeyer) whereby we implement a “system” to operate our company. As part of this system we have defined what we call our “Proven Process”. This is something we will show all prospective clients, and have on our website, that explains what it looks like to work with us. Starting at the beginning of the project to completion.

Project Description:

TLV is looking for graphic artist assistance in designing the following pieces:

1. Graphic depiction of “The TLV Way”, otherwise known as our “Proven Process”. The first attachments labeled TLV will show what we have done ourselves. These will show the general steps we have defined in both a sort of graphic way and a step by step narrative. The second attachment shows you some actual examples other firms have put together, hopefully that will show you what we are asking you to develop for us. Note that we are very open to any suggested clarifications or improvements to what we have done which may include changing phrases or saying something in a different way. Remember we are accountants!

2. We have defined our core values as a company, and we are wanting to develop some posters/placards so we can post them in our conference rooms, break room, etc. Attached are our core values as well as some deeper narratives about what they mean. Also included are many of the “words” we kicked around before arriving at our core values.

3. You will also find an attachment with our logo that should be incorporated, as well. Designs SHOULD INCLUDE, but not be limited to, the colors on our logo. Our end product should reflect a strong sense of our core values.

We would like to have the project in a form that would give us the option to use any/all of the information on our website, posters, brochures, etc.

Thanks in advance for your assistance.

Target Market(s)

Entrepreneurs and their companies with revenue greater than one million; Industries such as real estate, construction, trades and professional services; all in the Greater Houston Texas area

Industry/Entity Type

Accounting

Font styles to use
Serif
Other font styles liked:
• We are okay with Serif but are open.

Requirements
Must have
• Proven Process must be presented in a way that is clear and makes sense.
Nice to have
• Clean lines
• Colors should go with logo (see attached)
Should not have
• Can't think of anything - unless I see it

```html
<!DOCTYPE html>
<html lang="en">
<head>
<meta charset="utf-8">
<title>TLV Client Service Approach</title>
<link href="https://fonts.googleapis.com/css2?family=Archivo+Black&family=Arimo:wght@400;700&family=Tinos&display=swap" rel="stylesheet">
<style>
  :root {
    --page-bg: #e8e8e8;
    --slide-bg: #ffffff;
    --edge: #0a0a0a;
    --forest: #1c4620;
    --ring-outer: #fbf7cc;
    --ring-green: #d9ecc9;
    --ring-grey: #c9c9cb;
    --core-yellow: #fadf6a;
    --icon-ring: #8a8a8a;
    --brand-olive: #6b6a2a;
  }
  html, body {
    margin: 0;
    padding: 0;
    width: 1200px;
    height: 1200px;
    overflow: hidden;
    background: var(--page-bg);
  }
  .slide {
    position: absolute;
    left: 312px;
    width: 576px;
    height: 432px;
    display: block;
  }
  .slide--layers { top: 124px; }
  .slide--trio { top: 644px; }
  .slide-title {
    font-family: "Archivo Black", "Arial Black", sans-serif;
    font-size: 24px;
    fill: var(--forest);
  }
  .layer-label {
    font-family: "Arimo", Arial, sans-serif;
    font-size: 11.5px;
    fill: var(--forest);
  }
  .pillar-label {
    font-family: "Arimo", Arial, sans-serif;
    font-weight: 700;
    font-size: 17px;
    fill: #ffffff;
  }
  .brand-mark,
  .brand-name,
  .brand-tagline {
    font-family: "Tinos", "Times New Roman", serif;
    fill: var(--brand-olive);
  }
  .brand-mark { font-size: 24px; }
  .brand-name { font-size: 17px; }
  .brand-tagline { font-size: 10px; letter-spacing: 5px; }
</style>
</head>
<body>

<svg class="slide slide--layers" viewBox="0 0 720 540" aria-label="Client service approach, layered view">
  <rect width="720" height="540" fill="var(--slide-bg)"/>
  <rect x="708" y="0" width="12" height="540" fill="var(--edge)"/>
  <text class="slide-title" x="37" y="70">CLIENT SERVICE APPROACH</text>

  <g class="layers">
    <circle cx="360" cy="275" r="155" fill="var(--ring-outer)"/>
    <circle cx="360" cy="305" r="125" fill="var(--ring-green)"/>
    <polygon points="340,183 360,168 380,183" fill="var(--ring-green)"/>
    <circle cx="360" cy="337" r="93" fill="var(--ring-grey)"/>
    <polygon points="343,247 360,231 377,247" fill="var(--ring-grey)"/>
    <circle cx="360" cy="368" r="62" fill="var(--core-yellow)"/>
    <polygon points="346,309 360,294 374,309" fill="var(--core-yellow)"/>
  </g>

  <g class="layer-icons">
    <circle cx="360" cy="146" r="11" fill="var(--forest)" role="img" aria-label="Peace of mind icon"/>
    <circle cx="360" cy="208" r="12" fill="var(--forest)" role="img" aria-label="Client focus icon"/>
    <circle cx="360" cy="273" r="12" fill="var(--forest)" role="img" aria-label="Caring touch icon"/>
    <polygon points="340,430 340,408 360,395 380,408 380,430" fill="none" stroke="var(--forest)" stroke-width="1.2"/>
    <rect x="347" y="410" width="26" height="14" rx="3" fill="var(--forest)" role="img" aria-label="Handshake icon"/>
  </g>

  <g class="layer-labels">
    <text class="layer-label" x="401" y="154" text-anchor="middle">Peace of</text>
    <text class="layer-label" x="401" y="169" text-anchor="middle">mind</text>
    <text class="layer-label" x="399" y="208" text-anchor="middle">Client</text>
    <text class="layer-label" x="399" y="222" text-anchor="middle">focus</text>
    <text class="layer-label" x="395" y="270" text-anchor="middle">Caring</text>
    <text class="layer-label" x="395" y="284" text-anchor="middle">touch</text>
    <text class="layer-label" x="360" y="366" text-anchor="middle">Long term</text>
    <text class="layer-label" x="360" y="380" text-anchor="middle">relationships</text>
  </g>

  <g class="brand">
    <text class="brand-mark" x="171" y="456" text-anchor="middle">TLV</text>
    <text class="brand-name" x="171" y="482" text-anchor="middle">Ashdown, Pettifer &amp; Associates, PC</text>
    <line x1="36" y1="488" x2="306" y2="488" stroke="var(--brand-olive)" stroke-width="0.8"/>
    <text class="brand-tagline" x="171" y="503" text-anchor="middle">CPAs &amp; Advisors</text>
  </g>
</svg>

<svg class="slide slide--trio" viewBox="0 0 720 540" aria-label="Client service approach, three pillars">
  <rect width="720" height="540" fill="var(--slide-bg)"/>
  <rect x="708" y="0" width="12" height="540" fill="var(--edge)"/>
  <text class="slide-title" x="37" y="70">CLIENT SERVICE APPROACH</text>

  <g class="pillars">
    <circle cx="360" cy="200" r="73" fill="var(--forest)"/>
    <circle cx="282" cy="339" r="73" fill="var(--forest)"/>
    <circle cx="438" cy="339" r="73" fill="var(--forest)"/>
    <circle cx="360" cy="270" r="60" fill="#ffffff"/>
    <polygon points="348,214 360,196 372,214" fill="#ffffff"/>
    <polygon points="305,292 295,308 313,312" fill="#ffffff"/>
    <polygon points="415,292 425,308 407,312" fill="#ffffff"/>
    <circle cx="360" cy="265" r="22" fill="var(--forest)" role="img" aria-label="Advisor with headset icon"/>
  </g>

  <g class="pillar-icons">
    <circle cx="280" cy="143" r="42" fill="#ffffff" stroke="var(--icon-ring)" stroke-width="1"/>
    <circle cx="280" cy="143" r="20" fill="var(--forest)" role="img" aria-label="Client focus icon"/>
    <circle cx="190" cy="329" r="42" fill="#ffffff" stroke="var(--icon-ring)" stroke-width="1"/>
    <circle cx="190" cy="329" r="20" fill="var(--forest)" role="img" aria-label="Caring touch icon"/>
    <circle cx="530" cy="329" r="42" fill="#ffffff" stroke="var(--icon-ring)" stroke-width="1"/>
    <circle cx="530" cy="329" r="20" fill="var(--forest)" role="img" aria-label="Peace of mind icon"/>
  </g>

  <g class="pillar-labels">
    <text class="pillar-label" x="360" y="162" text-anchor="middle">Client</text>
    <text class="pillar-label" x="360" y="184" text-anchor="middle">focus</text>
    <text class="pillar-label" x="281" y="351" text-anchor="middle">Caring</text>
    <text class="pillar-label" x="281" y="373" text-anchor="middle">touch</text>
    <text class="pillar-label" x="438" y="351" text-anchor="middle">Peace of</text>
    <text class="pillar-label" x="438" y="373" text-anchor="middle">mind</text>
  </g>

  <g class="brand">
    <text class="brand-mark" x="171" y="456" text-anchor="middle">TLV</text>
    <text class="brand-name" x="171" y="482" text-anchor="middle">Ashdown, Pettifer &amp; Associates, PC</text>
    <line x1="36" y1="488" x2="306" y2="488" stroke="var(--brand-olive)" stroke-width="0.8"/>
    <text class="brand-tagline" x="171" y="503" text-anchor="middle">CPAs &amp; Advisors</text>
  </g>
</svg>

</body>
</html>
```